Bonusheft für Patienten als kleine DIN A6 Broschüre
Zielgruppe
Bonusheft für Patienten als kleine DIN A6 Broschüre in der Zahn-Prophylaxe. Die Texte haben wir bereits vollständig formuliert, auch die Gliederung ist vorgegeben.
Wir sind eine Zahnarztpraxis mit dem Schwerpunkt Prophylaxe. Für unsere Prophylaxeabteilung möchten wir eine DIN A6 Broschüre entwerfen lassen, die als Bonusheft für Patienten dient.
Inhalt: Informationen über unsere Praxis, die leitende Mitarbeiterin, individuelle Risiken und Empfehlungen der Patienten. Auch Fakten und Tipps zur Verbesserung der Mundhygiene und Putzgewohnheiten werden Beschrieben.
Aufgabenstellung
Broschüre als DIN A6 Bonusheft mit circa sieben gestalteten Seiten, bei denen wir den Aufbau und die exakten Texte bereits vollständig vorgeben. Zusätzlich folgen mehrere gleiche Seiten, bei denen die Termine und Stempel eingetragen werden (ca. fünf Seiten).
Für Ihre Orientierung haben wir unsere Fotos und Farbschema von vorhandenen Designs unserer Praxis bereitgestellt.
Orientieren Sie sich gerne an unserer vorhandenen Homepage im Hinblick auf unseren Stil und das Praxislogo.
Homepage: www.zahnpflege-am-lindenbogen.de
Wir stellen einige Fotos zur Verwendung bereit. Falls nötig, verwenden Sie auch Stock Fotos.
Im folgenden werden wir den gewünschten Aufbau mit den Texten je Seite detailliert vorstellen. Ihre Aufgabe ist es, dies in ein modernes, frisches, ansprechendes und kompetentes Design umzusetzen.
1. Seite / Cover
- Mit Praxislogo
- Text: „Mein Prophylaxepass“
2. Seite:
- Überschrift: „Sie lassen nicht jeden an Ihre Zähne? Wir auch nicht.“
-Text: „Herzlich Willkommen! Mein Name ist Wiebke und ich arbeite als leitende Mitarbeiterin im Prophylaxe Zentrum Talbrück. Momentan befinde ich mich in der Weiterbildung zur Dentalhygienikerin und bin begeistert von der Arbeit in der präventiven Zahnmedizin. Mit meinem Wissen und meiner Erfahrung möchte ich dazu beitragen, dass unsere Patienten sich bei uns wohl und gut betreut fühlen. Ich freue mich darauf, Ihnen zu helfen, Ihre Zahngesundheit zu erhalten und zu verbessern!“
- Foto einer Mitarbeiterin
4. Seite:
- Überschrift: „Die professionelle Zahnreinigung – Wellness & Prävention“
- Text: „Eine wichtige Präventionsmaßnahme ist die regelmäßige Zahnreinigung in unserem Prophylaxe-Zentrum. Karies, Mundgeruch und Zahnfleischerkrankungen werden effektiv vorgebeugt. Die Zahnreinigung ist ein Teil der individuell geplanten Prophylaxe und eine sinnvolle Ergänzung der häus..

```html
<!DOCTYPE html>
<html lang="de">
<head>
<meta charset="utf-8">
<title>Mein Prophylaxepass – Bonusheft</title>
<link href="https://fonts.googleapis.com/css2?family=Jost:wght@400;500;600;700&display=swap" rel="stylesheet">
<style>
:root{
  --bg:#e9e9ea;
  --paper:#ffffff;
  --khaki:#c8c2a4;
  --khaki-dark:#aea78a;
  --khaki-light:#e6e2d2;
  --ink:#3b3b3a;
  --muted:#6f6f6c;
  --sky:#cfe0e6;
  --brick:#9a7a62;
}
*{box-sizing:border-box;margin:0;padding:0}
html,body{width:1200px;height:3839px;overflow:hidden}
body{background:var(--bg);font-family:"Jost",sans-serif;color:var(--ink)}
.panel{position:relative;height:768px;display:flex;align-items:center;justify-content:center}
.panel + .panel{border-top:1px solid #dedede}
.spread{display:flex;box-shadow:0 18px 40px rgba(0,0,0,.14)}
.page{position:relative;width:330px;height:466px;background:var(--paper);overflow:hidden}
.page.left{border-right:1px solid #e2e2e2}
.footer-band{position:absolute;left:0;right:0;bottom:0;height:20px;background:var(--khaki);font-size:6px;color:#fff;padding:6px 14px;letter-spacing:.3px}
.page-no{position:absolute;bottom:26px;width:22px;height:16px;background:var(--ink);color:#fff;font-size:8px;font-weight:600;text-align:center;line-height:16px;border-radius:3px}
.left .page-no{right:14px}
.right .page-no{right:14px}
.mini-logo{position:absolute;top:12px;right:14px;text-align:right;font-size:7px;font-weight:500;color:var(--ink);display:flex;align-items:center;gap:4px}
.mini-logo .dot{width:7px;height:7px;background:var(--khaki)}
.kicker{color:var(--khaki-dark);font-weight:600;text-transform:uppercase;font-size:15px;line-height:1.1}
.headline{color:var(--ink);font-weight:700;text-transform:uppercase;font-size:15px;line-height:1.1}
.body-text{font-size:7.4px;line-height:1.55;color:var(--ink)}
.photo{position:absolute}
/* cover */
.cover{position:relative;width:370px;height:524px;background:var(--paper);overflow:hidden;box-shadow:0 18px 40px rgba(0,0,0,.16)}
.cover-photo{position:absolute;left:0;top:0;width:100%;height:350px;background:linear-gradient(180deg,var(--sky) 0%,#e2ebea 45%,#c9b8a6 70%,#b9b39a 100%)}
.cover-logo{position:absolute;left:20px;top:20px;background:#fff;padding:12px 16px;border-radius:4px;display:flex;align-items:center;gap:8px}
.cover-logo .sq{width:14px;height:14px;background:var(--khaki)}
.cover-logo .name{font-size:15px;font-weight:400;color:var(--ink);line-height:1.1}
.cover-logo .team{font-size:7px;color:var(--muted);margin-top:4px}
.cover-title{position:absolute;left:30px;top:392px}
.cover-title .kicker{font-size:30px}
.cover-title .headline{font-size:32px}
.cover-band{position:absolute;left:0;right:0;bottom:0;height:28px;background:var(--khaki)}
/* lists */
.check-list{list-style:none}
.check-list li{display:flex;align-items:center;gap:10px;font-size:9px;margin-bottom:9px}
.box{width:9px;height:9px;border:1px solid var(--khaki-dark);border-radius:2px;flex:none}
/* forms */
.card{position:absolute;left:18px;right:18px;border:1px solid var(--khaki);border-radius:6px;background:#fff;overflow:hidden}
.card-head{background:var(--khaki);color:#fff;font-size:6.5px;padding:5px 8px;display:flex;align-items:center;gap:6px}
.card-head .line{flex:1;height:9px;background:#fff;border-radius:2px}
.row{display:flex;align-items:center;gap:8px;font-size:6px;padding:5px 8px;color:var(--ink)}
.row .label{width:28px;font-weight:500}
.opt{display:flex;align-items:center;gap:3px}
.opt i{width:7px;height:7px;border:1px solid var(--khaki-dark);border-radius:50%;display:inline-block}
.stamp{margin:3px 8px 7px;width:70px;height:26px;background:var(--khaki-light);border-radius:4px;font-size:5.5px;color:var(--muted);padding:4px}
</style>
</head>
<body>

<section class="panel">
  <div class="cover">
    <div class="cover-photo" role="img" aria-label="Foto des Praxisgebäudes aus Backstein vor hellem Himmel"></div>
    <div class="cover-logo">
      <span class="sq"></span>
      <div><div class="name">Zahnpflege am Lindenbogen</div><div class="team">Dr. Lena Hartwig mit Team</div></div>
    </div>
    <div class="cover-title">
      <div class="kicker">Mein</div>
      <div class="headline">Prophylaxepass</div>
    </div>
    <div class="cover-band"></div>
  </div>
</section>

<section class="panel">
  <div class="spread">
    <div class="page left">
      <div class="mini-logo"><span class="dot"></span>Zahnpflege am Lindenbogen</div>
      <div style="position:absolute;left:20px;top:40px;width:210px">
        <div class="kicker" style="font-size:13px">Sie lassen nicht jeden an Ihre Zähne?</div>
        <div class="headline" style="font-size:15px;margin-top:3px">Wir auch nicht.</div>
        <p class="body-text" style="margin-top:10px">„Herzlich Willkommen! Mein Name ist Wiebke und ich arbeite als leitende Mitarbeiterin im Prophylaxe Zentrum Talbrück. Momentan befinde ich mich in der Weiterbildung zur Dentalhygienikerin und bin begeistert von der Arbeit in der präventiven Zahnmedizin. Mit meinem Wissen und meiner Erfahrung möchte ich dazu beitragen, dass unsere Patienten sich bei uns wohl und gut betreut fühlen. Ich freue mich darauf, Ihnen zu helfen, Ihre Zahngesundheit zu erhalten und zu verbessern!“</p>
      </div>
      <div class="photo" role="img" aria-label="Foto der leitenden Prophylaxe-Mitarbeiterin mit Zahnmodell" style="left:150px;top:210px;width:180px;height:236px;background:linear-gradient(180deg,#f4f4f2 0%,#d9d4cc 40%,#4f7d74 100%)"></div>
      <div class="page-no" style="bottom:26px">02</div>
      <div class="footer-band">www.zahnpflege-am-lindenbogen.de</div>
    </div>
    <div class="page right">
      <div class="mini-logo"><span class="dot"></span>Zahnpflege am Lindenbogen</div>
      <div style="position:absolute;left:20px;top:40px;width:290px">
        <div class="kicker" style="font-size:13px">Die professionelle Zahnreinigung –</div>
        <div class="headline" style="font-size:14px;margin-top:3px">Wellness &amp; Prävention</div>
        <p class="body-text" style="margin-top:10px">Eine wichtige Präventionsmaßnahme ist die regelmäßige Zahnreinigung in unserem Prophylaxe-Zentrum. Karies, Mundgeruch und Zahnfleischerkrankungen werden effektiv vorgebeugt. Die Zahnreinigung ist ein Teil der individuell geplanten Prophylaxe und eine sinnvolle Ergänzung der häuslichen Zahnpflege. Gerade an den Stellen, wo die eigene Zahnbürste nicht hinkommt, entfernen wir Beläge und Verfärbungen sanft und gründlich.</p>
      </div>
      <div style="position:absolute;left:0;right:0;top:250px;height:176px;background:var(--khaki-light)"></div>
      <div class="photo" role="img" aria-label="Foto einer lächelnden Patientin im Behandlungsstuhl" style="left:20px;top:262px;width:170px;height:164px;background:linear-gradient(135deg,#dfe8ec 0%,#e9d8c4 50%,#c7a77f 100%)"></div>
      <div style="position:absolute;left:200px;top:272px;width:112px;background:#fff;border-radius:5px;padding:8px" class="body-text">Natürlich weiße Zähne und ein frisches Gefühl: Nach der Reinigung sind Ihre Zähne glatt und strahlend. Erleben Sie Ihre Prophylaxe ganz entspannt.</div>
      <div class="page-no">03</div>
      <div class="footer-band"></div>
    </div>
  </div>
</section>

<section class="panel">
  <div class="spread">
    <div class="page left">
      <div class="mini-logo"><span class="dot"></span>Zahnpflege am Lindenbogen</div>
      <div class="photo" role="img" aria-label="Foto des Praxisteams im Gespräch mit Patienten" style="left:0;top:34px;width:330px;height:170px;background:linear-gradient(180deg,#e8eef0 0%,#c9d3d6 55%,#9fb3b8 100%)"></div>
      <div style="position:absolute;left:20px;top:222px;width:290px">
        <div class="kicker" style="font-size:14px">Moderne Technik</div>
        <div class="headline" style="font-size:14px;margin-top:3px">für eine bessere Behandlung</div>
        <p class="body-text" style="margin-top:10px">Für unsere Prophylaxebehandlungen nutzen wir aktuelle Behandlungsmethoden und setzen auf moderne Technologie wie das Pulverstrahl-System. Dadurch gewährleisten wir für unsere Patienten eine feine und angenehme Behandlung. Gleichzeitig stellen wir eine ausgezeichnete Behandlungsqualität sicher, welche Ihre Zähne nachhaltig schützt und Krankheiten vorbeugt.</p>
      </div>
      <div class="page-no">04</div>
      <div class="footer-band">www.zahnpflege-am-lindenbogen.de</div>
    </div>
    <div class="page right">
      <div class="mini-logo"><span class="dot"></span>Zahnpflege am Lindenbogen</div>
      <div style="position:absolute;left:30px;top:70px">
        <div class="kicker" style="font-size:14px;margin-bottom:16px">Risikoanalyse</div>
        <ul class="check-list">
          <li><span class="box"></span>Kariesaktivität</li>
          <li><span class="box"></span>Empfindliches Zahnfleisch</li>
          <li><span class="box"></span>Erosionen / Säureschäden</li>
          <li><span class="box"></span>Zahnschmelzverlust</li>
          <li><span class="box"></span>Weicher Zahnschmelz</li>
          <li><span class="box"></span>Halitosis (Mundgeruch)</li>
          <li><span class="box"></span>Zahnverfärbungen</li>
          <li><span class="box"></span>Rauchen</li>
          <li><span class="box"></span>Retainer</li>
        </ul>
      </div>
      <div class="page-no">05</div>
      <div class="footer-band"></div>
    </div>
  </div>
</section>

<section class="panel">
  <div class="spread">
    <div class="page left">
      <div class="mini-logo"><span class="dot"></span>Zahnpflege am Lindenbogen</div>
      <div style="position:absolute;left:30px;top:90px">
        <div class="kicker" style="font-size:14px">Ergänzende</div>
        <div class="headline" style="font-size:14px;margin:3px 0 16px">Pflegetipps</div>
        <ul class="check-list">
          <li><span class="box"></span>1. Zahnseide</li>
          <li><span class="box"></span>2. Superfloss</li>
          <li><span class="box"></span>3. Zahnseidesticks</li>
          <li><span class="box"></span>4. Interdentalbürstchen</li>
          <li><span class="box"></span>5. Zungenreinigung</li>
          <li><span class="box"></span>6. Intensiv Fluoridierung</li>
          <li><span class="box"></span>7. 1x wöchentliche Spezial Zahnpasta</li>
          <li><span class="box"></span>8. Munddusche</li>
          <li><span class="box"></span>9. Mundspüllösung</li>
        </ul>
      </div>
      <div class="page-no">06</div>
      <div class="footer-band">www.zahnpflege-am-lindenbogen.de</div>
    </div>
    <div class="page right">
      <div class="mini-logo"><span class="dot"></span>Zahnpflege am Lindenbogen</div>
      <div class="card" style="top:44px">
        <div class="card-head">Name:<span class="line"></span></div>
        <div class="row"><span class="label">Prophylaxe Pass überreicht am:</span></div>
        <div class="row"><span class="label">Risikostufe:</span><span class="opt"><i></i>3 Monate</span><span class="opt"><i></i>4 Monate</span><span class="opt"><i></i>6 Monate</span><span class="opt"><i></i>12 Monate</span></div>
        <div class="row"><span class="label">Ihr Intervall:</span><span class="opt"><i></i>3 Monate</span><span class="opt"><i></i>4 Monate</span></div>
      </div>
      <div class="card" style="top:168px">
        <div class="card-head">Ihr nächster Termin:<span class="line"></span></div>
        <div class="row"><span class="label">Intervall:</span><span class="opt"><i></i>3 Monate</span><span class="opt"><i></i>4 Monate</span><span class="opt"><i></i>6 Monate</span><span class="opt"><i></i>12 Monate</span></div>
        <div class="row"><span class="label">Termin:</span><span class="opt"><i></i>Regulärer Termin</span><span class="opt"><i></i>Kompakttermin</span></div>
        <div class="stamp">Stempel &amp; Unterschrift</div>
      </div>
      <div class="card" style="top:284px">
        <div class="card-head">Ihr nächster Termin:<span class="line"></span></div>
        <div class="row"><span class="label">Intervall:</span><span class="opt"><i></i>3 Monate</span><span class="opt"><i></i>4 Monate</span><span class="opt"><i></i>6 Monate</span><span class="opt"><i></i>12 Monate</span></div>
        <div class="row"><span class="label">Termin:</span><span class="opt"><i></i>Regulärer Termin</span><span class="opt"><i></i>Kompakttermin</span></div>
        <div class="stamp">Stempel &amp; Unterschrift</div>
      </div>
      <div class="page-no">07</div>
      <div class="footer-band"></div>
    </div>
  </div>
</section>

<section class="panel">
  <div class="spread">
    <div class="page left">
      <div class="mini-logo"><span class="dot"></span>Zahnpflege am Lindenbogen</div>
      <div class="card" style="top:44px">
        <div class="card-head">Ihr nächster Termin:<span class="line"></span></div>
        <div class="row"><span class="label">Intervall:</span><span class="opt"><i></i>3 Monate</span><span class="opt"><i></i>4 Monate</span><span class="opt"><i></i>6 Monate</span><span class="opt"><i></i>12 Monate</span></div>
        <div class="row"><span class="label">Termin:</span><span class="opt"><i></i>Regulärer Termin</span><span class="opt"><i></i>Kompakttermin</span></div>
        <div class="stamp">Stempel &amp; Unterschrift</div>
      </div>
      <div class="card" style="top:160px">
        <div class="card-head">Ihr nächster Termin:<span class="line"></span></div>
        <div class="row"><span class="label">Intervall:</span><span class="opt"><i></i>3 Monate</span><span class="opt"><i></i>4 Monate</span><span class="opt"><i></i>6 Monate</span><span class="opt"><i></i>12 Monate</span></div>
        <div class="row"><span class="label">Termin:</span><span class="opt"><i></i>Regulärer Termin</span><span class="opt"><i></i>Kompakttermin</span></div>
        <div class="stamp">Stempel &amp; Unterschrift</div>
      </div>
      <div class="card" style="top:276px">
        <div class="card-head">Ihr nächster Termin:<span class="line"></span></div>
        <div class="row"><span class="label">Intervall:</span><span class="opt"><i></i>3 Monate</span><span class="opt"><i></i>4 Monate</span><span class="opt"><i></i>6 Monate</span><span class="opt"><i></i>12 Monate</span></div>
        <div class="row"><span class="label">Termin:</span><span class="opt"><i></i>Regulärer Termin</span><span class="opt"><i></i>Kompakttermin</span></div>
        <div class="stamp">Stempel &amp; Unterschrift</div>
      </div>
      <div class="page-no">08</div>
      <div class="footer-band">www.zahnpflege-am-lindenbogen.de</div>
    </div>
    <div class="page right">
      <div class="mini-logo"><span class="dot"></span>Zahnpflege am Lindenbogen</div>
      <div class="card" style="top:44px">
        <div class="card-head">Ihr nächster Termin:<span class="line"></span></div>
        <div class="row"><span class="label">Intervall:</span><span class="opt"><i></i>3 Monate</span><span class="opt"><i></i>4 Monate</span><span class="opt"><i></i>6 Monate</span><span class="opt"><i></i>12 Monate</span></div>
        <div class="row"><span class="label">Termin:</span><span class="opt"><i></i>Regulärer Termin</span><span class="opt"><i></i>Kompakttermin</span></div>
        <div class="stamp">Stempel &amp; Unterschrift</div>
      </div>
      <div class="card" style="top:160px">
        <div class="card-head">Ihr nächster Termin:<span class="line"></span></div>
        <div class="row"><span class="label">Intervall:</span><span class="opt"><i></i>3 Monate</span><span class="opt"><i></i>4 Monate</span><span class="opt"><i></i>6 Monate</span><span class="opt"><i></i>12 Monate</span></div>
        <div class="row"><span class="label">Termin:</span><span class="opt"><i></i>Regulärer Termin</span><span class="opt"><i></i>Kompakttermin</span></div>
        <div class="stamp">Stempel &amp; Unterschrift</div>
      </div>
      <div class="card" style="top:276px">
        <div class="card-head">Ihr nächster Termin:<span class="line"></span></div>
        <div class="row"><span class="label">Intervall:</span><span class="opt"><i></i>3 Monate</span><span class="opt"><i></i>4 Monate</span><span class="opt"><i></i>6 Monate</span><span class="opt"><i></i>12 Monate</span></div>
        <div class="row"><span class="label">Termin:</span><span class="opt"><i></i>Regulärer Termin</span><span class="opt"><i></i>Kompakttermin</span></div>
        <div class="stamp">Stempel &amp; Unterschrift</div>
      </div>
      <div class="page-no">09</div>
      <div class="footer-band"></div>
    </div>
  </div>
</section>

</body>
</html>
```